High Tech Real Estate Startup needs a business card

We are developing an innovative real estate marketing product based around advanced search and virtual reality.

We talk to people, we need business cards.

Target Market(s)

The target market is technology professionals and realtors.

Contact Information for Business Card

The information to be included will include

Name
Title
Phone Number
E-mail Address
www.zelquin.com

It should use simple iconography for each one of those fields.

Font styles to use
Other font styles liked:
• Co, Jubilat, Avenir

Colors

Designer to choose colors to be used in the design.

Requirements
Must have
• Clean aesthetic,
• Good use of negative space.
• It should use our company logo, shown in the attached file. It is able to use the negative of that logo (coloured font and white background) and I have attached other acceptable accent colours in a swatch file.
Should not have
• Should not be too busy
• No extraneous text (slogans, tag lines etc)

```html
<!DOCTYPE html>
<html lang="en">
<head>
<meta charset="utf-8">
<title>Zelquin Business Card</title>
<link rel="stylesheet" href="https://fonts.googleapis.com/css2?family=Montserrat:wght@500&family=Inter:wght@400;500&display=swap">
<style>
  :root {
    --teal: #17b6bd;
    --charcoal: #232323;
    --charcoal-soft: #2e2e2e;
    --ink: #1e1e1e;
    --paper: #ffffff;
    --stage: #e9e8e6;
  }
  * { box-sizing: border-box; margin: 0; padding: 0; }
  html, body { width: 1200px; height: 930px; overflow: hidden; }
  body { background: var(--stage); position: relative; font-family: "Inter", sans-serif; }

  .card {
    position: absolute;
    width: 620px;
    height: 354px;
    border-radius: 18px;
    overflow: hidden;
    box-shadow: 0 6px 18px rgba(0,0,0,0.18);
  }

  /* Back side */
  .card-back { left: 90px; top: 90px; background: var(--charcoal); }
  .card-back .network-art {
    position: absolute; inset: 0;
    background: radial-gradient(ellipse at 55% 40%, var(--charcoal-soft) 0%, var(--charcoal) 70%);
  }
  .card-back .brand-name {
    position: absolute; left: 0; right: 0; top: 148px;
    text-align: center;
    font-family: "Montserrat", sans-serif; font-weight: 500;
    font-size: 62px; letter-spacing: 2px; color: var(--teal);
  }

  /* Front side */
  .card-front { left: 490px; top: 486px; background: var(--paper); }
  .card-front .corner-swoosh { position: absolute; inset: 0; }
  .card-front .brand-name {
    position: absolute; right: 110px; top: 46px;
    font-family: "Montserrat", sans-serif; font-weight: 500;
    font-size: 52px; letter-spacing: 2px; color: var(--teal);
  }
  .card-front .name-row {
    position: absolute; left: 34px; top: 168px; width: 500px;
    display: flex; align-items: flex-end; gap: 10px;
  }
  .card-front .person-name {
    font-weight: 500; font-size: 21px; color: var(--teal); text-transform: uppercase; white-space: nowrap;
  }
  .card-front .rule { flex: 1; height: 1.5px; background: var(--teal); margin-bottom: 4px; }
  .card-front .person-title { position: absolute; left: 34px; top: 198px; font-size: 15px; color: var(--ink); }
  .card-front .address { position: absolute; left: 34px; top: 226px; font-size: 15px; line-height: 19px; color: var(--ink); }
  .card-front .contact-list {
    position: absolute; left: 34px; top: 272px; list-style: none;
    font-size: 15px; line-height: 21px; color: var(--ink);
  }
  .card-front .contact-list li { display: flex; align-items: center; gap: 8px; }
  .card-front .contact-list svg { width: 11px; height: 11px; flex: none; }
</style>
</head>
<body>

  <section class="card card-back">
    <div class="network-art" role="img" aria-label="Faint grey constellation network of connected dots across the dark card"></div>
    <div class="brand-name">ZELQUIN</div>
  </section>

  <section class="card card-front">
    <svg class="corner-swoosh" viewBox="0 0 620 354" aria-hidden="true">
      <path d="M532 0 Q512 250 312 354 L620 354 L620 0 Z" fill="var(--teal)"/>
      <path d="M546 0 Q528 258 334 354 L620 354 L620 0 Z" fill="var(--charcoal)"/>
    </svg>

    <div class="brand-name">ZELQUIN</div>

    <div class="name-row">
      <span class="person-name">Daniel Harper</span>
      <span class="rule"></span>
    </div>
    <div class="person-title">Director</div>
    <div class="address">417 Cedar Ridge Ln.<br>Franklin, TN 37064</div>

    <ul class="contact-list">
      <li>
        <svg viewBox="0 0 12 12"><path d="M2.5 1 L4.5 1 L5.2 3.4 L3.9 4.3 Q4.8 6.6 7.7 8.1 L8.6 6.8 L11 7.5 L11 9.5 Q10.5 11 9 11 Q1 10 1 2.6 Q1 1.2 2.5 1 Z" fill="var(--teal)"/></svg>
        +1-555-214-7730
      </li>
      <li>
        <svg viewBox="0 0 12 12"><rect x="1" y="2.5" width="10" height="7" fill="none" stroke="var(--teal)" stroke-width="1.2"/><path d="M1 2.5 L6 6.5 L11 2.5" fill="none" stroke="var(--teal)" stroke-width="1.2"/></svg>
        hello@zelquin.com
      </li>
      <li>
        <svg viewBox="0 0 12 12"><circle cx="6" cy="6" r="5" fill="none" stroke="var(--teal)" stroke-width="1.1"/><ellipse cx="6" cy="6" rx="2.2" ry="5" fill="none" stroke="var(--teal)" stroke-width="1"/><path d="M1 6 H11" stroke="var(--teal)" stroke-width="1"/></svg>
        www.zelquin.com
      </li>
    </ul>
  </section>

</body>
</html>
```